Web Instant Messenger Design Project

Hello,
The project consist of designing a web instant messenger interface. What we need is a Photoshop file that contains the design elements of this app. (windows, buttons , dropdowns etc)
notes:
- we are looking for the same look and feel as the now closed Trevlo.com
- the name of the app will be chatnook.com , or similar.
- the application will be browser based, will cover 100% of the browser area.
- please don't make a "flat" background.
I attached 3 screen captures that shows the graphic elements we need :
img1: -
is the login "page" with username and password fields. There are also a connect & disconnect buttons + a register one
img2:
a) We have the classic friend list that shows who is online and their status. The friend list window can be moved and has 7
buttons (down:add friedn, delete friend, create group,change friend group and create conference / up: conference room list
and mass message buttons)
b) There is a conversation window that can be dragged. The conversation window will keep the private conversations and
conferences as a tab bar. Please note the key field area .
c) Mass Message window - here you can select the group and/or friends, write the message and hit send.
img3
a) on friend list window , when you click one of the down button a new , non movable window will appear. In this window you will have actions corresponding to the button you clicked : add/ delete friend , create conference , etc
b) public room window- is a drag-able window with the conferences you can join.
c)the conversation window with a conference selected. There is a invite buddy drop down, a list of participants and the conversations zone. On participants list there will be a kick and ban button.(not present in this capture)
Updates
When submitting a design please try to provide a mock of the "friend list window". Thank you and sorry if this info comes too late.
Industry/Entity Type
Group
Look and feel
Each slider illustrates characteristics of the customer's brand and the style your logo design should communicate.

```html
<!DOCTYPE html>
<html lang="en">
<head>
<meta charset="utf-8">
<title>chatnook – Mass Message</title>
<link href="https://fonts.googleapis.com/css2?family=Cabin:wght@400;600;700&display=swap" rel="stylesheet">
<style>
:root{
  --page:#e2e2e2;
  --page-dot:#d3d3d3;
  --header-top:#0d5e93;
  --header-mid:#0f6aa0;
  --header-bottom:#094a76;
  --panel:#f4f4f4;
  --panel-line:#cfcfcf;
  --group:#dcdcdc;
  --row:#f6f6f6;
  --text:#333333;
  --muted:#8a8a8a;
  --teal:#3aa6c4;
  --teal-dark:#237f9b;
  --accent:#1a74b5;
  --scrim:rgba(40,40,40,.22);
  --online:#6fb5c9;
  --offline:#c2c2c2;
}
*{box-sizing:border-box;margin:0;padding:0}
html,body{width:1200px;height:700px;overflow:hidden}
body{position:relative;background-color:var(--page);background-image:radial-gradient(circle,var(--page-dot) 1px,transparent 1.3px),radial-gradient(circle,var(--page-dot) 1px,transparent 1.3px);background-size:6px 6px;background-position:0 0,3px 3px;font-family:"Cabin",Arial,sans-serif;color:var(--text);font-size:14px}
.abs{position:absolute}
.topbar{left:0;top:0;width:1200px;height:37px;background:linear-gradient(90deg,var(--header-bottom),var(--header-mid) 45%,var(--header-bottom))}
.brand{left:118px;top:2px;display:flex;align-items:center;gap:8px;color:#e9f3f8;font-size:27px;font-weight:600;letter-spacing:.5px}
.brand-mark{width:24px;height:24px;background:#e9f3f8;border-radius:50%}
.panel{background:var(--panel);border:1px solid var(--panel-line)}
.panel-title{position:absolute;left:0;right:0;top:0;height:38px;border-bottom:1px solid var(--panel-line);display:flex;align-items:center;padding-left:16px;gap:10px;font-weight:700;font-size:14px;background:linear-gradient(#fafafa,#eeeeee)}
.btn{background:linear-gradient(var(--teal),var(--teal-dark));color:#fff;border:1px solid #1e6f88;border-radius:3px;font-size:13px;display:flex;align-items:center;justify-content:center}
.group{position:absolute;left:0;right:0;height:28px;background:var(--group);border-top:1px solid #c8c8c8;border-bottom:1px solid #c8c8c8;display:flex;align-items:center;padding-left:15px;font-weight:700;font-size:13px}
.row{position:absolute;left:0;right:0;height:38px;background:var(--row);border-bottom:1px solid #dedede;display:flex;align-items:center;padding-left:23px;font-size:15px}
.row .state{margin-left:auto;margin-right:43px;font-size:11px;font-style:italic;color:var(--muted)}
.toggle{margin-left:auto;margin-right:18px;font-size:16px;color:#777;font-weight:400}
.tab{top:97px;height:22px;background:#f0f0f0;border:1px solid #ccc;display:flex;align-items:center;font-size:13px}
.tab span{flex:1;padding-left:16px}
.tab b{width:22px;border-left:1px solid #ccc;text-align:center;font-size:12px}
.field{background:#fff;border:1px solid #ccc}
.scrim{inset:0;background:var(--scrim)}
.modal{left:327px;top:118px;width:609px;height:445px;background:#f2f2f2;border:1px solid #bdbdbd;box-shadow:0 2px 10px rgba(0,0,0,.3)}
.modal-head{position:absolute;left:0;right:0;top:0;height:37px;background:linear-gradient(#ffffff,#ededed);border-bottom:1px solid #d4d4d4;display:flex;align-items:center;padding-left:17px;gap:12px;font-weight:700;font-size:14px}
.close{margin-left:auto;margin-right:16px;color:var(--accent);font-size:15px;font-weight:700}
.picker{left:11px;top:48px;width:250px;height:346px;border:1px solid #cfcfcf;overflow:hidden}
.picker .group{padding-left:8px;gap:7px}
.picker .row{padding-left:15px;gap:7px;background:#fafafa}
.picker .row .state{margin-right:8px}
.picker .row svg.chat{margin-right:18px}
.box{width:13px;height:13px;background:#fff;border:1px solid #c4c4c4;border-radius:2px;display:inline-flex;align-items:center;justify-content:center}
.composer{left:272px;top:48px;width:326px;height:347px;padding:13px 12px;font-size:14px}
.footer-icons{position:absolute;left:0;right:0;bottom:0;height:32px;border-top:1px solid var(--panel-line);display:flex;justify-content:space-around;align-items:center;background:#ededed}
</style>
</head>
<body>

<header class="abs topbar"></header>
<div class="abs brand"><span class="brand-mark"></span>chatnook</div>

<section class="abs panel friend-list" style="left:112px;top:50px;width:250px;height:611px">
  <div class="panel-title">
    <svg width="24" height="16" viewBox="0 0 24 16"><circle cx="8" cy="5" r="4" fill="#333"/><path d="M0 16c0-5 4-7 8-7s8 2 8 7z" fill="#333"/><circle cx="17" cy="5" r="3.3" fill="#555"/><path d="M13 10c4-2 11-1 11 6h-7z" fill="#555"/></svg>
    Friend List
  </div>
  <div class="abs btn" style="left:8px;top:46px;width:111px;height:31px">Mass Message</div>
  <div class="abs btn" style="left:128px;top:46px;width:111px;height:31px;justify-content:flex-start;padding-left:10px">R.......</div>
  <div class="abs" style="left:62px;top:89px;font-size:13px">Status</div>
  <div class="abs field" style="left:113px;top:85px;width:110px;height:22px;border-radius:3px;display:flex;align-items:center;gap:8px;padding-left:10px;font-size:13px">
    <svg width="16" height="13" viewBox="0 0 16 13"><path d="M1 1h10v7H5l-3 3V8H1z" fill="#9bb0bb"/><path d="M12 4h3v6h-1v2l-2-2H7V9h5z" fill="#b8c8cf"/></svg>Online
  </div>
  <div class="group" style="top:118px">Buddies</div>
  <div class="row" style="top:147px">Ionut<span class="state">Online</span></div>
  <div class="row" style="top:185px">Admin<span class="state">Ofline</span></div>
  <div class="row" style="top:223px">Cre1<span class="state">Ofline</span></div>
  <div class="group" style="top:261px">Kostel</div>
  <div class="row" style="top:290px">Big<span class="state">Ofline</span></div>
  <div class="row" style="top:328px">Bigbig<span class="state">Online</span></div>
  <div class="row" style="top:366px">Cre2<span class="state">Ofline</span></div>
  <div class="group" style="top:404px">Toba</div>
  <div class="row" style="top:433px">Bubu<span class="state">Online</span></div>
  <div class="row" style="top:471px">Vasile<span class="state">Ofline</span></div>
  <div class="row" style="top:509px">Crern12<span class="state" style="margin-right:8px">Ofline</span><svg style="margin-right:19px" width="16" height="13" viewBox="0 0 16 13"><path d="M1 1h10v7H5l-3 3V8H1z" fill="var(--offline)"/><path d="M12 4h3v6h-1v2l-2-2H7V9h5z" fill="#d6d6d6"/></svg></div>
  <div class="group" style="top:547px">Work<span class="toggle">+</span></div>
  <div class="footer-icons">
    <svg width="20" height="18" viewBox="0 0 20 18"><circle cx="8" cy="5" r="4" fill="#6a9a3a"/><path d="M1 18c0-6 3-8 7-8s7 2 7 8z" fill="#6a9a3a"/><path d="M15 11h2v2h2v2h-2v2h-2v-2h-2v-2h2z" fill="#4f8a2a"/></svg>
    <svg width="22" height="18" viewBox="0 0 22 18"><circle cx="7" cy="5" r="3.5" fill="#5d8ea6"/><circle cx="14" cy="5" r="3.5" fill="#4a7c96"/><path d="M0 18c0-6 3-8 7-8s7 2 7 8zM9 18c0-6 2-8 5-8s6 2 6 8z" fill="#5d8ea6"/></svg>
    <svg width="20" height="18" viewBox="0 0 20 18"><circle cx="8" cy="5" r="4" fill="#c55a2a"/><path d="M1 18c0-6 3-8 7-8s7 2 7 8z" fill="#c55a2a"/><rect x="13" y="13" width="7" height="2" fill="#a7441a"/></svg>
    <svg width="20" height="18" viewBox="0 0 20 18"><circle cx="8" cy="5" r="4" fill="#8a8a8a"/><path d="M1 18c0-6 3-8 7-8s7 2 7 8z" fill="#8a8a8a"/><path d="M13 14l2 2 4-4" stroke="#555" stroke-width="2" fill="none"/></svg>
    <svg width="20" height="18" viewBox="0 0 20 18"><circle cx="6" cy="5" r="3.5" fill="#2c6aa6"/><circle cx="14" cy="5" r="3.5" fill="#d9a52a"/><path d="M0 18c0-6 3-8 6-8s6 2 6 8zM8 18c0-6 3-8 6-8s6 2 6 8z" fill="#2c6aa6" opacity=".9"/></svg>
  </div>
</section>

<section class="abs panel conversations" style="left:372px;top:50px;width:715px;height:611px">
  <div class="panel-title">
    <svg width="20" height="18" viewBox="0 0 20 18"><path d="M2 1h16v11H8l-5 5v-5H2z" fill="#333"/></svg>
    Your Conversations
  </div>
  <div class="abs" style="left:0;right:0;top:78px;height:30px;background:#cfcfcf;border-top:1px solid #c2c2c2;border-bottom:1px solid #c2c2c2"></div>
  <div class="abs" style="right:16px;top:120px;font-size:13px">(at least 4 characters)</div>
  <div class="abs field" style="left:13px;top:140px;width:689px;height:23px"></div>
  <div class="abs field" style="left:13px;top:172px;width:689px;height:386px"></div>
  <div class="abs field" style="left:13px;top:567px;width:573px;height:31px"></div>
  <div class="abs btn" style="left:594px;top:567px;width:109px;height:31px">Send Message</div>
</section>
<div class="abs tab" style="left:386px;width:93px"><span>Ionut</span><b>✕</b></div>
<div class="abs tab" style="left:486px;width:93px"><span>Cre1</span><b>✕</b></div>
<div class="abs tab" style="left:587px;width:93px"><span>Cre2</span><b>✕</b></div>
<div class="abs tab" style="left:688px;width:95px"><span>Bubu</span><b>✕</b></div>
<div class="abs tab" style="left:790px;width:94px"><span>vasile</span><b>✕</b></div>
<div class="abs tab" style="left:892px;width:93px"><span style="padding-left:8px">Crerm12</span><b>✕</b></div>

<div class="abs scrim"></div>

<section class="abs modal" role="dialog" aria-label="Mass Message">
  <div class="modal-head">
    <svg width="16" height="12" viewBox="0 0 16 12"><rect width="16" height="12" fill="#333"/><path d="M0 0l8 7 8-7" stroke="#fff" stroke-width="1.4" fill="none"/></svg>
    Mass Message<span class="close">x</span>
  </div>
  <div class="abs picker">
    <div class="group" style="top:-1px;height:30px"><span class="box"></span>Buddies<span class="toggle">+</span></div>
    <div class="group" style="top:29px;height:29px"><span class="box"><svg width="11" height="11" viewBox="0 0 11 11"><path d="M1 6l3 3 6-8" stroke="#888" stroke-width="1.6" fill="none"/></svg></span>Kostel<span class="toggle">–</span></div>
    <div class="row" style="top:58px"><span class="box"><svg width="11" height="11" viewBox="0 0 11 11"><path d="M1 6l3 3 6-8" stroke="#888" stroke-width="1.6" fill="none"/></svg></span>Big<span class="state">Ofline</span><svg class="chat" width="16" height="13" viewBox="0 0 16 13"><path d="M1 1h10v7H5l-3 3V8H1z" fill="var(--offline)"/><path d="M12 4h3v6h-1v2l-2-2H7V9h5z" fill="#d6d6d6"/></svg></div>
    <div class="row" style="top:96px"><span class="box"><svg width="11" height="11" viewBox="0 0 11 11"><path d="M1 6l3 3 6-8" stroke="#888" stroke-width="1.6" fill="none"/></svg></span>Bigbig<span class="state">Online</span><svg class="chat" width="16" height="13" viewBox="0 0 16 13"><path d="M1 1h10v7H5l-3 3V8H1z" fill="var(--online)"/><path d="M12 4h3v6h-1v2l-2-2H7V9h5z" fill="#9fcfdc"/></svg></div>
    <div class="row" style="top:134px"><span class="box"><svg width="11" height="11" viewBox="0 0 11 11"><path d="M1 6l3 3 6-8" stroke="#888" stroke-width="1.6" fill="none"/></svg></span>Cre2<span class="state">Ofline</span><svg class="chat" width="16" height="13" viewBox="0 0 16 13"><path d="M1 1h10v7H5l-3 3V8H1z" fill="var(--offline)"/><path d="M12 4h3v6h-1v2l-2-2H7V9h5z" fill="#d6d6d6"/></svg></div>
    <div class="group" style="top:172px;height:29px"><span class="box"></span>Toba<span class="toggle">–</span></div>
    <div class="row" style="top:201px"><span class="box"><svg width="11" height="11" viewBox="0 0 11 11"><path d="M1 6l3 3 6-8" stroke="#888" stroke-width="1.6" fill="none"/></svg></span>Bubu<span class="state">Online</span><svg class="chat" width="16" height="13" viewBox="0 0 16 13"><path d="M1 1h10v7H5l-3 3V8H1z" fill="var(--online)"/><path d="M12 4h3v6h-1v2l-2-2H7V9h5z" fill="#9fcfdc"/></svg></div>
    <div class="row" style="top:239px"><span class="box"><svg width="11" height="11" viewBox="0 0 11 11"><path d="M1 6l3 3 6-8" stroke="#888" stroke-width="1.6" fill="none"/></svg></span>Vasile<span class="state">Ofline</span><svg class="chat" width="16" height="13" viewBox="0 0 16 13"><path d="M1 1h10v7H5l-3 3V8H1z" fill="var(--offline)"/><path d="M12 4h3v6h-1v2l-2-2H7V9h5z" fill="#d6d6d6"/></svg></div>
    <div class="row" style="top:277px"><span class="box"></span>Crern12<span class="state">Ofline</span><svg class="chat" width="16" height="13" viewBox="0 0 16 13"><path d="M1 1h10v7H5l-3 3V8H1z" fill="var(--offline)"/><path d="M12 4h3v6h-1v2l-2-2H7V9h5z" fill="#d6d6d6"/></svg></div>
    <div class="group" style="top:315px;height:31px"><span class="box"></span>Work<span class="toggle">+</span></div>
  </div>
  <div class="abs field composer">Mass Message</div>
  <div class="abs btn" style="left:488px;top:401px;width:109px;height:30px">Send Mass</div>
</section>

</body>
</html>
```